Webdesign für Heilpraktiker
Zielgruppe
Ich bin Heilpraktiker und betreibe eine Naturheilpraxis mit den Schwerpunkten der traditionellen chinesischen Medizin (TCM). Da ganz besonders in der Philosophie (sogenannte 'Schule' des Wo Shen). Aber auch in der traditionellen Heilweise der TCM, wie Akupunktur, Heilkräutermedizin und weiteres.
Die Zielgruppe sind Menschen, die medizinische Hilfe benötigen. (Vom Kind bis zum älteren Menschen).
Aufgabenstellung
Es gibt ein Praxislogo, ein Foto von mir und ggf. ein Landschaftsbild. Ich dachte an fünf Hauptseiten mit Untergruppen. Am Ende sollte alles in Wordpress formatiert werden können, um es zu veröffentlichen.
Weitere Fotos zur Unterstützung der Themen kann ich natürlich gerne liefern.
Die Gestaltung ist nicht festgesetzt. Sollte aber seriös rüber kommen.

```html
<!DOCTYPE html>
<html lang="de">
<head>
<meta charset="utf-8">
<title>Naturheilpraxis Jonas Werthmann</title>
<link href="https://fonts.googleapis.com/css2?family=Lato:wght@300;400;700;900&display=swap" rel="stylesheet">
<style>
:root{
  --gold:#d9a967;
  --dark:#232323;
  --footer:#1f1f1f;
  --text:#2b2b2b;
  --muted:#9a9a9a;
  --white:#ffffff;
}
*{margin:0;padding:0;box-sizing:border-box}
html,body{width:1200px;height:976px;overflow:hidden;background:var(--white);font-family:'Lato',sans-serif;color:var(--text)}
.page{position:relative;width:1200px;height:976px}
.main-nav{position:absolute;top:0;left:0;width:1200px;height:39px;background:var(--dark);display:flex;padding-left:150px}
.main-nav a{display:block;height:39px;line-height:39px;padding:0 24px;color:var(--white);font-size:11.5px;font-weight:700;text-decoration:none;text-transform:uppercase}
.main-nav a.active{background:var(--gold);color:var(--dark)}
.hero{position:absolute;top:39px;left:0;width:1200px;height:439px;
  background:linear-gradient(180deg,#c9cfcf 0%,#9aa79a 16%,#6f8a4a 34%,#7f9b3c 55%,#8aa443 78%,#6e8a34 100%)}
.brand-badge{position:absolute;left:525px;top:10px;width:150px;height:150px;border-radius:50%;background:rgba(255,255,255,.35);display:flex;align-items:center;justify-content:center}
.brand-badge .inner{width:128px;height:128px;border-radius:50%;background:var(--white);display:flex;align-items:center;justify-content:center;text-align:center;font-size:13px;font-weight:700;color:var(--dark);line-height:1.3}
.hero-title{position:absolute;top:181px;left:0;width:1200px;text-align:center;color:var(--white);font-size:42px;line-height:48px;font-weight:400}
.hero-title strong{font-weight:900}
.hero-title .light{font-weight:300}
.phone-btn{position:absolute;left:472px;top:301px;width:256px;height:43px;border-radius:22px;background:var(--dark);color:var(--white);display:flex;align-items:center;justify-content:center;gap:12px;font-size:19px;font-weight:700;letter-spacing:.3px}
.portrait{position:absolute;left:698px;top:437px;width:352px;height:383px;background:linear-gradient(135deg,#7b7e85 0%,#b9bcc1 45%,#2a2e38 100%)}
.about{position:absolute;left:150px;top:524px;width:480px}
.about h1{color:var(--gold);font-size:22px;font-weight:700;letter-spacing:2.5px;text-transform:uppercase}
.about .role{margin-top:6px;font-size:13px;line-height:15px}
.facts{list-style:none;margin-top:22px}
.facts li{display:flex;align-items:center;height:30px;font-size:13px;font-weight:400;color:var(--text)}
.facts svg{width:22px;height:22px;margin-right:16px;flex:none}
.site-footer{position:absolute;left:0;top:842px;width:1200px;height:134px;background:var(--footer);text-align:center}
.footer-links{margin-top:25px;font-size:11.5px;color:var(--muted);line-height:22px}
.footer-links span.sep{margin:0 14px}
.social{display:flex;justify-content:center;gap:22px;margin-top:20px}
.social i{display:block;width:14px;height:14px;border-radius:50%;background:#5a5a5a}
</style>
</head>
<body>
<div class="page">
  <nav class="main-nav">
    <a class="active">Startseite</a>
    <a>Zu meiner Person</a>
    <a>Wobei kann ich helfen</a>
    <a>Der erste Besuch</a>
    <a>Was ist das Wo Shen</a>
    <a>Kontakt</a>
  </nav>

  <header class="hero" role="img" aria-label="Landschaftsfoto: grüne Berge und Täler unter bewölktem Himmel">
    <div class="brand-badge"><div class="inner">Praxis<br>Werthmann</div></div>
    <h2 class="hero-title"><strong>Naturheilpraxis</strong> <span class="light">des</span><br>Heilpraktiker Jonas Werthmann</h2>
    <div class="phone-btn">
      <svg width="20" height="20" viewBox="0 0 24 24" fill="none" stroke="#fff" stroke-width="1.6"><path d="M5 3h4l2 5-2.5 1.5a11 11 0 0 0 6 6L16 13l5 2v4a2 2 0 0 1-2 2A17 17 0 0 1 3 5a2 2 0 0 1 2-2z"/><path d="M15 3a6 6 0 0 1 6 6M15 7a2 2 0 0 1 2 2"/></svg>
      0531 – 478 52 90
    </div>
  </header>

  <div class="portrait" role="img" aria-label="Porträtfoto des Heilpraktikers im Sakko"></div>

  <section class="about">
    <h1>Jonas Werthmann</h1>
    <p class="role">Heilpraktiker und zertifizierter Therapeut der traditionellen chinesischen Medizin (Berufsverband VNH e.V.)</p>
    <ul class="facts">
      <li><svg viewBox="0 0 24 24" fill="none" stroke-width="1.8"><path d="M20 9a9 9 0 1 1-3-5" stroke="#2b2b2b"/><path d="M7 11l4 4 9-10" stroke="#d9a967"/></svg>Jahrgang 1967</li>
      <li><svg viewBox="0 0 24 24" fill="none" stroke-width="1.8"><path d="M20 9a9 9 0 1 1-3-5" stroke="#2b2b2b"/><path d="M7 11l4 4 9-10" stroke="#d9a967"/></svg>Seit 2006 Heilpraktiker in Braunschweig</li>
      <li><svg viewBox="0 0 24 24" fill="none" stroke-width="1.8"><path d="M20 9a9 9 0 1 1-3-5" stroke="#2b2b2b"/><path d="M7 11l4 4 9-10" stroke="#d9a967"/></svg>Seit 2010 Gründer und Leiter des KLW Blutanalyselabors in Braunschweig</li>
      <li><svg viewBox="0 0 24 24" fill="none" stroke-width="1.8"><path d="M20 9a9 9 0 1 1-3-5" stroke="#2b2b2b"/><path d="M7 11l4 4 9-10" stroke="#d9a967"/></svg>Seit 2015 zertifizierter TCM Therapeut (Berufsverband VNH e.V.)</li>
      <li><svg viewBox="0 0 24 24" fill="none" stroke-width="1.8"><path d="M20 9a9 9 0 1 1-3-5" stroke="#2b2b2b"/><path d="M7 11l4 4 9-10" stroke="#d9a967"/></svg>Beschäftigung mit der Wo Shen Philosophie (Schule) seit 1988</li>
    </ul>
  </section>

  <footer class="site-footer">
    <div class="footer-links">
      Startseite<span class="sep">|</span>Zu meiner Person<span class="sep">|</span>Wobei kann ich helfen<span class="sep">|</span>Der erste Besuch<span class="sep">|</span>Was ist das Wo Shen<span class="sep">|</span>Kontakt<br>
      Impressum<span class="sep">|</span>Datenschutzerklärung
    </div>
    <div class="social" aria-label="Soziale Netzwerke">
      <i></i><i></i><i></i><i></i><i></i>
    </div>
  </footer>
</div>
</body>
</html>
```